Vexmor Industries - Quality Campaign

Objective:

Create a visually engaging graphic design that promotes quality awareness and engagement within Vexmor Industries. The design should convey the core values of quality at Vexmor, emphasizing its four key elements:

Zero Defects, Zero Scrap
Customer Satisfaction
First Time Right
Product Performance
Target Audience:

Vexmor Industries employees at all levels.

Usage:

The design will be used for various purposes, including:

Posters displayed in common areas and workstations
Presentation slides for internal meetings and training sessions
Design Requirements:

Visual Style: The design should be modern, professional, and visually appealing. It should evoke a sense of pride in quality and inspire team members to strive for excellence.
Color Palette: Consider using the Vexmor Industries brand colors or a complementary palette that reflects quality and professionalism (see website: https://www.vexmor-industries.example/).
Key Elements: The four key elements of quality should be clearly visible and integrated into the design. This could be achieved through text, icons, or a combination of both.
Vexmor Industries Logo: A vector file of the Vexmor Industries logo will be provided. Optional use of the logo is encouraged to maintain brand consistency.
Call to Action: The design should include a clear call to action, such as "Embrace Quality," "Strive for Excellence," or "Own Your Quality."
Additional Considerations:

Versatility: The design should be adaptable for different formats and sizes (e.g., posters, presentations, social media posts).
Memorability: The design should be memorable and easily recognizable as representing Vexmor Industries' commitment to quality.
Deliverables:

High-resolution digital files in various formats suitable for printing and digital use.
By adhering to these guidelines, the winning design will effectively communicate the importance of quality at Vexmor Industries and inspire employees to embrace these values in their daily work.

Industry/Entity Type

Engineering, manufacturing, semi-conductor, optics

Requirements
Must have
• Reference to Quality and 4 key elements

```html
<!DOCTYPE html>
<html lang="en">
<head>
<meta charset="utf-8">
<title>Vexmor Industries – Embrace Quality</title>
<link rel="stylesheet" href="https://fonts.googleapis.com/css2?family=Barlow:wght@600;700&family=Roboto:wght@500&display=swap">
<style>
  :root {
    --brand-blue: #4f86c6;
    --field-blue: #5a8bc8;
    --field-light: #86a8d6;
    --header-bg: #f4f7f2;
    --white: #ffffff;
    --gold-light: #e6dfae;
    --gold-mid: #d8c98a;
  }
  * { margin: 0; padding: 0; box-sizing: border-box; }
  html, body { width: 900px; height: 1200px; overflow: hidden; }
  body { position: relative; background: var(--field-blue); font-family: "Barlow", sans-serif; }

  .header {
    position: absolute; left: 0; top: 0; width: 900px; height: 122px;
    background: var(--header-bg);
  }
  .brand-mark {
    position: absolute; left: 28px; top: 28px; width: 77px; height: 77px;
    background: var(--brand-blue);
  }
  .brand-name {
    position: absolute; left: 117px; top: 30px;
    font-family: "Roboto", sans-serif; font-weight: 500;
    font-size: 35px; line-height: 36px; color: var(--brand-blue);
  }

  .field {
    position: absolute; left: 0; top: 122px; width: 900px; height: 1078px;
    background: radial-gradient(ellipse 60% 55% at 50% 50%, var(--field-light) 0%, var(--field-blue) 100%);
  }

  .headline { position: absolute; left: 0; top: 0; color: var(--white); font-weight: 700; }
  .headline-small {
    position: absolute; left: 102px; top: 222px;
    font-size: 90px; line-height: 1; letter-spacing: 1px; white-space: nowrap;
  }
  .headline-large {
    position: absolute; left: 96px; top: 308px;
    font-size: 222px; line-height: 1; letter-spacing: -3px; white-space: nowrap;
  }

  .podium-art {
    position: absolute; left: 140px; top: 478px; width: 620px; height: 400px;
    border-radius: 40% 40% 50% 50% / 20% 20% 30% 30%;
    background: radial-gradient(ellipse 60% 60% at 50% 55%, var(--gold-light) 0%, rgba(216,201,138,0.55) 60%, rgba(216,201,138,0) 100%);
  }

  .pillars {
    position: absolute; left: 0; top: 975px; width: 900px; height: 170px;
    list-style: none;
  }
  .pillar {
    position: absolute; top: 0; width: 200px; margin-left: -100px;
    text-align: center; color: var(--white);
  }
  .pillar-icon { display: block; width: 44px; height: 44px; margin: 0 auto; }
  .pillar-label {
    display: block; margin-top: 32px;
    font-weight: 600; font-size: 25px; line-height: 32px; letter-spacing: 0.5px;
  }
  .divider {
    position: absolute; top: 1022px; width: 4px; height: 117px;
    background: var(--white); border-radius: 2px;
  }
</style>
</head>
<body>
  <header class="header">
    <div class="brand-mark"></div>
    <div class="brand-name">Vexmor<br>Industries</div>
  </header>

  <main class="field"></main>

  <div class="podium-art" role="img" aria-label="Gold first-place medal on a white pillar, a second medal and a gold trophy on a round cream podium"></div>

  <h1 class="headline">
    <span class="headline-small">Embrace</span>
    <span class="headline-large">Quality.</span>
  </h1>

  <ul class="pillars">
    <li class="pillar" style="left:176px">
      <svg class="pillar-icon" viewBox="0 0 44 44" aria-hidden="true">
        <rect x="10" y="4" width="24" height="36" rx="7" fill="none" stroke="#fff" stroke-width="6"/>
      </svg>
      <span class="pillar-label">Zero Defects<br>Zero Scrap</span>
    </li>
    <li class="pillar" style="left:355px">
      <svg class="pillar-icon" viewBox="0 0 44 44" aria-hidden="true">
        <g fill="#fff">
          <polygon points="8,4 9.8,8 14,8.4 10.8,11 11.8,15 8,12.8 4.2,15 5.2,11 2,8.4 6.2,8"/>
          <polygon points="22,0 23.8,4 28,4.4 24.8,7 25.8,11 22,8.8 18.2,11 19.2,7 16,4.4 20.2,4"/>
          <polygon points="36,4 37.8,8 42,8.4 38.8,11 39.8,15 36,12.8 32.2,15 33.2,11 30,8.4 34.2,8"/>
          <rect x="4" y="20" width="36" height="22" rx="8"/>
        </g>
      </svg>
      <span class="pillar-label">Customer<br>Satisfaction</span>
    </li>
    <li class="pillar" style="left:544px">
      <svg class="pillar-icon" viewBox="0 0 44 44" aria-hidden="true">
        <circle cx="22" cy="22" r="21" fill="#fff"/>
        <polyline points="13,22 19,28 31,16" fill="none" stroke="#6e97cd" stroke-width="3.5" stroke-linecap="round" stroke-linejoin="round"/>
      </svg>
      <span class="pillar-label">First Time<br>Right</span>
    </li>
    <li class="pillar" style="left:730px">
      <svg class="pillar-icon" viewBox="0 0 44 44" aria-hidden="true">
        <path d="M8 36 A18 18 0 1 1 36 36" fill="none" stroke="#fff" stroke-width="6" stroke-dasharray="10 3"/>
        <line x1="22" y1="24" x2="30" y2="34" stroke="#fff" stroke-width="5" stroke-linecap="round"/>
      </svg>
      <span class="pillar-label">Product<br>Performance</span>
    </li>
  </ul>
  <div class="divider" style="left:253px"></div>
  <div class="divider" style="left:451px"></div>
  <div class="divider" style="left:633px"></div>
</body>
</html>
```